Business Card Design for Occupational Medicine Start Up Company

We need to design a professional business card. We are a healthcare company providing occupational medicine services to blue collar industries. We are professional, efficient and high quality service providers.

Target Market(s)

Blue Collar Industry: Shipbuilding, Ports, Trucking Companies; The Executives and Safety Officers for these companies

Industry/Entity Type

Healthcare

Contact Information for Business Card

Logo, Name, Title, Email, Phone

Other font styles liked:
• Please match our Brand Guide

Requirements
Must have
• Our Company Colors and Logo

```html
<!DOCTYPE html>
<html lang="en">
<head>
<meta charset="utf-8">
<title>Harborline Clinics – Business Card</title>
<link href="https://fonts.googleapis.com/css2?family=Montserrat:wght@400;500;600;700&display=swap" rel="stylesheet">
<style>
  :root {
    --stage: #242424;
    --navy: #2e3173;
    --sky: #2a9bd8;
    --amber: #f0a534;
    --paper: #f2f2f0;
    --ink: #2f3170;
    --lavender: #7d80e6;
    --white: #ffffff;
  }
  * { margin: 0; padding: 0; box-sizing: border-box; }
  html, body { width: 1200px; height: 1200px; overflow: hidden; }
  body {
    background: var(--stage);
    font-family: "Montserrat", Arial, sans-serif;
    position: relative;
  }
  .card {
    position: absolute;
    width: 593px;
    height: 348px;
    border-radius: 20px;
    overflow: hidden;
  }
  .card--front { left: 298px; top: 198px; background: var(--navy); }
  .card--back { left: 292px; top: 637px; background: var(--paper); }

  /* front */
  .front-brand {
    position: absolute;
    left: 0; right: 0; top: 118px;
    text-align: center;
    color: var(--lavender);
    font-weight: 700;
    font-size: 30px;
    letter-spacing: 2px;
    line-height: 1.15;
  }
  .front-brand .dot {
    display: block;
    width: 22px; height: 22px;
    border-radius: 50%;
    background: var(--lavender);
    margin: 0 auto 14px;
  }
  .front-url {
    position: absolute;
    left: 0; right: 0; top: 301px;
    text-align: center;
    color: var(--white);
    font-size: 15px;
    font-weight: 500;
    letter-spacing: 1.6px;
  }
  .front-url .blue { color: var(--sky); }
  .front-url .amber { color: var(--amber); }

  /* back */
  .back-shape { position: absolute; inset: 0; width: 593px; height: 348px; }
  .back-brand {
    position: absolute;
    left: 20px; width: 262px; top: 92px;
    text-align: center;
    color: var(--white);
    font-weight: 700;
    font-size: 24px;
    letter-spacing: 1px;
    line-height: 1.2;
  }
  .back-brand .dot {
    display: block;
    width: 46px; height: 46px;
    border-radius: 50%;
    background: var(--sky);
    margin: 0 auto 14px;
  }
  .person { position: absolute; left: 333px; top: 76px; }
  .person-name {
    color: var(--sky);
    font-size: 25px;
    font-weight: 600;
    letter-spacing: 0.5px;
    line-height: 1.1;
  }
  .person-role {
    color: var(--ink);
    font-size: 16px;
    font-weight: 400;
    margin-top: 3px;
  }
  .contact { position: absolute; left: 333px; top: 144px; list-style: none; }
  .contact li {
    display: flex;
    align-items: flex-start;
    color: var(--ink);
    font-size: 15.5px;
    line-height: 21px;
  }
  .contact li + li { margin-top: 0.5px; }
  .contact li.address { margin-top: 18px; }
  .contact svg { width: 13px; height: 13px; margin: 4px 12px 0 0; flex: none; }
</style>
</head>
<body>

<section class="card card--front" aria-label="Card front">
  <div class="front-brand"><span class="dot"></span>HARBORLINE<br>CLINICS</div>
  <p class="front-url">www.<span class="blue">harborline</span><span class="amber">clinics</span>.com</p>
</section>

<section class="card card--back" aria-label="Card back">
  <svg class="back-shape" viewBox="0 0 593 348" aria-hidden="true">
    <path d="M0 0 H232 Q330 120 302 232 Q285 300 232 348 H0 Z" fill="var(--amber)"/>
    <path d="M0 0 H222 Q318 122 290 232 Q274 300 232 348 H0 Z" fill="var(--navy)"/>
  </svg>

  <div class="back-brand"><span class="dot"></span>HARBORLINE<br>CLINICS</div>

  <div class="person">
    <p class="person-name">DANA REYES</p>
    <p class="person-role">Senior Doctor</p>
  </div>

  <ul class="contact">
    <li>
      <svg viewBox="0 0 16 16"><path d="M3 2h3l1.5 3.5-2 1.3a8 8 0 0 0 3.7 3.7l1.3-2L14 10v3a1 1 0 0 1-1 1A12 12 0 0 1 2 3a1 1 0 0 1 1-1z" fill="var(--sky)"/></svg>
      555-014-2380
    </li>
    <li>
      <svg viewBox="0 0 16 16"><rect x="1" y="3" width="14" height="10" fill="var(--ink)"/><path d="M1.5 3.5 8 9l6.5-5.5" stroke="var(--paper)" stroke-width="1.4" fill="none"/></svg>
      care@harborline.com
    </li>
    <li>
      <svg viewBox="0 0 16 16"><circle cx="8" cy="8" r="6.5" fill="none" stroke="var(--amber)" stroke-width="1.5"/><ellipse cx="8" cy="8" rx="2.8" ry="6.5" fill="none" stroke="var(--amber)" stroke-width="1.2"/><path d="M1.5 8h13" stroke="var(--amber)" stroke-width="1.2"/></svg>
      www.harborline.com
    </li>
    <li class="address">
      <svg viewBox="0 0 16 16"><path d="M8 1a5 5 0 0 0-5 5c0 4 5 9 5 9s5-5 5-9a5 5 0 0 0-5-5z" fill="var(--amber)"/><circle cx="8" cy="6" r="2" fill="var(--paper)"/></svg>
      <span>48 Dock Street, Suite 210<br>Port Linden, State 20418</span>
    </li>
  </ul>
</section>

</body>
</html>
```